Business Card Design of an established Waste Management, Plastic Recycling and Renewable Energy Comp

We are looking for business card design for plastic card with holograms (Very similar to credit card). I will provide our logo (Quenbys). So the name on the business card will be our logo )Quenbys) + Environmental next to it, so it will read Quenbys Environmental. The font for Environmental does not to be the same as the font of the logo. The holograms will be used to display ISO14001 Certified (In normal credit card, normally on the holograms, they show nova or kelo). I will post the design requirements from the card printing company very shortly to make sure they can use the design for the plastic card.

Target Market(s)

Companies, Government Organizations, Corporations.

Industry/Entity Type

Business

Contact Information for Business Card

Motto (Under the logo): Let's Keep It Green
Name: Leopold Maresca; Position: Business Manager; Address: Pelmore Landfill & Recycling Facility, Tressingham Rd, Corvell Vale, WA 6190; Ph: +61 8 5210 4738; Mob: +61 455 903 172; E: Leo@quenbysenvironmental-mail.com

Requirements
Must have
• Business Names: Quenbys Logo + Environmental word after the logo.
• Motto (Under the logo): Let's Keep It Green
• All the Business Card Details above.
• Hologram Logo on the lower right corner which says: ISO 14001 Certified.
• Please remember the design will be printed on plastic card Not paper. The plastic crad is the same as credit card. Hope this helps. Thank You

```html
<!DOCTYPE html>
<html lang="en">
<head>
<meta charset="utf-8">
<title>Quenbys Environmental – Business Card</title>
<link href="https://fonts.googleapis.com/css2?family=Open+Sans:wght@400;600;700&family=Russo+One&display=swap" rel="stylesheet">
<style>
  :root {
    --page-bg: #dfe6ee;
    --card-bg: #f7f9fb;
    --card-edge: #c9d3de;
    --ink-dark: #2b2f36;
    --ink-mid: #3f4650;
    --brand-blue: #2f78c4;
    --brand-blue-deep: #1d4f9a;
    --badge-blue: #5b9bd8;
    --panel-dark: #2e3138;
    --panel-text: #dfe3e8;
  }
  * { margin: 0; padding: 0; box-sizing: border-box; }
  html, body {
    width: 800px; height: 1200px; overflow: hidden;
    background: var(--page-bg);
    font-family: "Open Sans", Arial, sans-serif;
  }
  .canvas { position: relative; width: 800px; height: 1200px; }

  .card {
    position: absolute; left: 150px;
    width: 500px; height: 284px;
    background: var(--card-bg);
    border: 1px solid var(--card-edge);
    border-radius: 6px;
    overflow: hidden;
    box-shadow: 0 10px 30px rgba(40, 60, 90, 0.15);
  }
  .card-front { top: 170px; }
  .card-back { top: 720px; }

  .brand { position: absolute; display: flex; align-items: center; gap: 10px; }
  .brand-dot { width: 34px; height: 34px; border-radius: 50%; background: var(--brand-blue); }
  .brand-name {
    font-weight: 600; font-size: 38px; line-height: 1;
    color: var(--ink-dark); letter-spacing: -0.5px;
  }
  .card-front .brand { left: 30px; top: 32px; }

  .cert-badge { position: absolute; right: 26px; top: 30px; width: 66px; height: 66px; }

  .wave { position: absolute; left: 0; top: 0; width: 500px; height: 284px; }

  .website {
    position: absolute; left: 28px; top: 152px;
    font-size: 12px; color: var(--ink-mid);
    display: flex; align-items: center; gap: 6px;
  }
  .website svg { width: 10px; height: 10px; }

  .contact { position: absolute; right: 24px; top: 172px; text-align: right; color: var(--panel-text); }
  .contact-name { font-weight: 700; font-size: 15px; color: var(--brand-blue); line-height: 20px; }
  .contact-role { font-size: 12px; color: var(--brand-blue-deep); line-height: 16px; margin-bottom: 10px; }
  .contact-line {
    font-size: 12px; line-height: 16px;
    display: flex; justify-content: flex-end; align-items: center; gap: 8px;
  }
  .contact-line svg { width: 10px; height: 10px; }

  .card-back .brand { left: 50%; top: 108px; transform: translateX(-50%); }
  .card-back .brand-dot { width: 44px; height: 44px; }
  .card-back .brand-name { font-size: 48px; }

  .motto {
    position: absolute; left: 0; right: 0; top: 206px;
    text-align: center;
    font-family: "Russo One", Arial, sans-serif;
    font-size: 14px; letter-spacing: 2px; color: var(--ink-dark);
  }
  .motto .accent { color: var(--brand-blue-deep); }

  .address {
    position: absolute; left: 0; right: 0; top: 232px;
    text-align: center; font-size: 13px; line-height: 17px; color: var(--ink-mid);
  }
</style>
</head>
<body>
<div class="canvas">

  <section class="card card-front" aria-label="Card front">
    <svg class="wave" viewBox="0 0 500 284" aria-hidden="true">
      <path d="M0 244 C120 300 250 180 340 130 C400 98 460 96 500 98 L500 104 C460 102 405 108 345 140 C255 190 125 300 0 250 Z" fill="#2f78c4"/>
      <path d="M95 284 C190 270 270 190 350 150 C410 120 460 116 500 118 L500 284 Z" fill="#2e3138"/>
      <path d="M95 284 C190 270 270 190 350 150 C410 120 460 116 500 118" fill="none" stroke="#8fb4de" stroke-width="1.5"/>
    </svg>

    <div class="brand">
      <span class="brand-dot"></span>
      <span class="brand-name">Quenbys</span>
    </div>

    <svg class="cert-badge" viewBox="0 0 66 66" role="img" aria-label="Certification badge">
      <circle cx="33" cy="33" r="31" fill="#5b9bd8"/>
    </svg>

    <div class="website">
      <svg viewBox="0 0 10 10" aria-hidden="true"><circle cx="5" cy="5" r="4.5" fill="#5b8fd0"/></svg>
      www.quenbysgroup-web.com
    </div>

    <div class="contact">
      <div class="contact-name">Leopold Maresca</div>
      <div class="contact-role">Business Manager</div>
      <div class="contact-line">+61 8 5210 4738
        <svg viewBox="0 0 10 10" aria-hidden="true"><path d="M2 1 L4 1 L5 3 L4 4 C4.5 5.5 5 6 6 6.5 L7 5.5 L9 6.5 L9 8.5 C5 9 1 5 2 1 Z" fill="#3a78c4"/></svg>
      </div>
      <div class="contact-line">+61 455 903 172
        <svg viewBox="0 0 10 10" aria-hidden="true"><rect x="2.5" y="0.5" width="5" height="9" rx="1" fill="none" stroke="#3a78c4"/></svg>
      </div>
      <div class="contact-line">Leo@quenbysenvironmental-mail.com
        <svg viewBox="0 0 10 10" aria-hidden="true"><rect x="0.5" y="2" width="9" height="6" fill="none" stroke="#3a78c4"/><path d="M0.5 2 L5 5.5 L9.5 2" fill="none" stroke="#3a78c4"/></svg>
      </div>
    </div>
  </section>

  <section class="card card-back" aria-label="Card back">
    <div class="brand">
      <span class="brand-dot"></span>
      <span class="brand-name">Quenbys</span>
    </div>
    <div class="motto">LET'S KEEP IT <span class="accent">GREEN</span></div>
    <div class="address">
      Pelmore Landfill &amp; Recycling Facility<br>
      Tressingham Rd, Corvell Vale, WA 6190
    </div>
  </section>

</div>
</body>
</html>
```